Brackwell Yard Services Flyer Design

I need a new flyer design for my business, Brackwell Yard Services. I’ll be providing my old flyer and logo as references. The new flyer should feature updated wording, contact information, logos, and photos, but still keep the original “What We Do” section and include the phrase “Don’t See? Just Ask!” somewhere near the services. The flyer needs to look great in black and white for door-to-door handouts but also be eye-catching and professional enough for social media use.

The updated content should include the headline “Transforming Outdoor Spaces with Hard Work & Precision” and highlight three main service areas: Landscaping Services (project-based landscaping to clean, prepare, and transform outdoor spaces with precision), Property Cleanup (quick hauls, debris removal, or full cleanouts—no job too big or small), and Ground Preparation (pad preparation, brush removal, and fire lines—making properties safe, functional, and project-ready).

Please also include a “Why Choose Us?” section that lists: Locally owned since 2022, Reliable & affordable – no corners cut, Professional results you can trust, LICENSED AND Insured, and Quality work / on time / references / flexible / follow-up.

At the bottom, include the contact details: Call or Text Today!
www.brackwellyard.example
| sales@brackwellyard.example
| (555) 014-7293

The overall design should be clean, professional, and easy to read with a layout that clearly shows what we offer. Use visuals that represent outdoor services, landscaping, and property cleanup/prep work. I want something that feels trustworthy, family-friendly, and modern.
Use the same photo of leaf clean up from the original flyer if possible.
Our company colors are also black and white. For the most part.

```html
<!DOCTYPE html>
<html lang="en">
<head>
<meta charset="utf-8">
<title>Brackwell Yard Services – Flyer</title>
<link rel="stylesheet" href="https://fonts.googleapis.com/css2?family=Anton&family=Bebas+Neue&family=Roboto+Condensed:wght@700&family=Source+Sans+3:wght@400;600&display=swap">
<style>
  :root {
    --orange: #f7941d;
    --black: #0d0d0d;
    --white: #ffffff;
    --ink: #1a1a1a;
    --page: #ffffff;
  }
  * { box-sizing: border-box; margin: 0; padding: 0; }
  html, body { width: 1200px; height: 761px; overflow: hidden; background: var(--page); }
  .sheet { position: relative; width: 1200px; height: 761px; }

  .flyer {
    position: absolute; top: 0; width: 590px; height: 761px;
    background: var(--white); overflow: hidden;
    font-family: "Source Sans 3", sans-serif; color: var(--ink);
  }
  .flyer--color { left: 0; --accent: var(--orange); --band: var(--orange); --tag-text: var(--white); }
  .flyer--mono  { left: 612px; --accent: var(--black); --band: var(--black); --tag-text: var(--white); }

  /* Header */
  .masthead {
    position: absolute; left: 0; top: 0; width: 590px; height: 66px;
    background: var(--band);
    clip-path: polygon(0 0,100% 0,100% 92%,92% 96%,84% 90%,75% 97%,66% 92%,55% 98%,44% 91%,33% 97%,22% 92%,12% 98%,0 93%);
  }
  .masthead__title {
    position: absolute; left: 18px; top: 9px;
    font-family: "Anton", sans-serif; font-size: 20.5px; line-height: 22px;
    color: var(--white); text-align: center; letter-spacing: 0.2px;
  }
  .masthead__brand {
    position: absolute; right: 14px; top: 14px; display: flex; align-items: center; gap: 6px;
    font-family: "Bebas Neue", sans-serif; font-size: 19px; line-height: 1; color: var(--white);
    width: 130px;
  }
  .masthead__brand-mark { width: 14px; height: 14px; border-radius: 50%; background: var(--white); flex: none; }

  /* Photos */
  .gallery { position: absolute; left: 0; top: 66px; width: 590px; height: 196px; }
  .photo { position: absolute; top: 0; height: 196px; width: 194px; }
  .photo--leaves { left: 0; }
  .photo--yard { left: 198px; }
  .photo--haul { left: 397px; width: 193px; }
  .flyer--color .photo--leaves { background: linear-gradient(160deg,#6f7a2a 0%,#a8842f 45%,#7a3f18 100%); }
  .flyer--color .photo--yard { background: linear-gradient(180deg,#7f9fbf 0%,#8e8f7e 35%,#a99c84 70%,#d8c8a6 100%); }
  .flyer--color .photo--haul { background: linear-gradient(170deg,#c69a6a 0%,#6e6a5c 45%,#8aa08f 75%,#315a9a 100%); }
  .flyer--mono .photo--leaves { background: linear-gradient(160deg,#6c6c6c 0%,#8e8e8e 45%,#404040 100%); }
  .flyer--mono .photo--yard { background: linear-gradient(180deg,#bdbdbd 0%,#7b7b7b 35%,#9a9a9a 70%,#d2d2d2 100%); }
  .flyer--mono .photo--haul { background: linear-gradient(170deg,#a8a8a8 0%,#4e4e4e 45%,#8c8c8c 75%,#3a3a3a 100%); }

  /* Tags */
  .tag {
    position: absolute; height: 32px; padding: 0 8px;
    background: var(--accent); color: var(--tag-text);
    font-family: "Roboto Condensed", sans-serif; font-weight: 700; font-size: 21px; line-height: 32px;
    clip-path: polygon(1% 4%,20% 0,45% 6%,70% 1%,99% 5%,100% 90%,80% 100%,55% 94%,30% 100%,0 95%);
  }
  .tag--services { left: 22px; top: 273px; width: 131px; }
  .tag--why { left: 22px; top: 545px; width: 175px; }
  .tag--what { left: 386px; top: 273px; width: 128px; }

  .divider { position: absolute; left: 351px; top: 288px; width: 1px; height: 393px; background: var(--accent); }

  .head {
    position: absolute; font-family: "Bebas Neue", sans-serif; font-size: 22px; line-height: 22px;
    color: var(--accent); white-space: nowrap;
  }
  .copy { position: absolute; left: 26px; width: 300px; font-size: 11px; line-height: 14px; }

  .list { position: absolute; list-style: none; font-size: 11px; line-height: 19.4px; }
  .list li { position: relative; padding-left: 16px; white-space: nowrap; }
  .list li::before {
    content: ""; position: absolute; left: 0; top: 4px; width: 11px; height: 10px; background: var(--accent);
    clip-path: polygon(25% 0,75% 0,100% 50%,75% 100%,25% 100%,0 50%);
  }

  .licensed {
    position: absolute; left: 0; width: 352px; top: 667px; text-align: center;
    font-family: "Bebas Neue", sans-serif; font-size: 18px; line-height: 18px; color: var(--accent);
  }
  .assurances { position: absolute; left: 0; width: 352px; top: 688px; text-align: center; font-size: 11px; line-height: 14px; }
  .assurances .dot { color: var(--accent); }
  .flyer--mono .assurances .dot { color: var(--ink); }

  .ask { position: absolute; left: 388px; top: 668px; font-family: "Bebas Neue", sans-serif; font-size: 18px; color: var(--accent); }

  /* Footer */
  .contact-bar {
    position: absolute; left: 0; top: 707px; width: 590px; height: 54px; background: var(--black);
    clip-path: polygon(0 8%,10% 2%,22% 7%,35% 0,48% 6%,60% 1%,73% 7%,86% 2%,100% 6%,100% 100%,0 100%);
  }
  .contact-bar__cta {
    position: absolute; top: 8px; left: 0; width: 590px; text-align: center;
    font-family: "Roboto Condensed", sans-serif; font-weight: 700; font-size: 20px; line-height: 22px; color: var(--accent);
  }
  .flyer--mono .contact-bar__cta, .flyer--mono .contact-bar__item { color: var(--white); }
  .contact-bar__line {
    position: absolute; top: 31px; left: 0; width: 590px; display: flex; justify-content: center; gap: 14px;
    font-family: "Roboto Condensed", sans-serif; font-weight: 700; font-size: 15px; line-height: 18px;
  }
  .contact-bar__item { display: flex; align-items: center; gap: 5px; color: var(--orange); }
  .contact-bar__item svg { width: 14px; height: 14px; flex: none; }
</style>
</head>
<body>
<div class="sheet">

  <!-- Colour edition -->
  <article class="flyer flyer--color">
    <header class="masthead">
      <h1 class="masthead__title">TRANSFORMING OUTDOOR SPACES<br>WITH HARD WORK &amp; PRECISION</h1>
      <div class="masthead__brand"><span class="masthead__brand-mark"></span>BRACKWELL YARD SERVICES</div>
    </header>
    <div class="gallery">
      <div class="photo photo--leaves" role="img" aria-label="Rake leaning on a full leaf bag on an autumn lawn"></div>
      <div class="photo photo--yard" role="img" aria-label="Backyard with gravel bed, paver wall and wooden fence"></div>
      <div class="photo photo--haul" role="img" aria-label="Trailer loaded with junk and debris for hauling"></div>
    </div>

    <div class="tag tag--services">Our Services</div>
    <h2 class="head" style="left:26px;top:318px;">LANDSCAPING SERVICES</h2>
    <p class="copy" style="top:349px;">Project-based landscaping to clean, prepare, and transform outdoor spaces with precision.</p>
    <h2 class="head" style="left:26px;top:393px;">GROUND PREPARATION</h2>
    <p class="copy" style="top:423px;">Pad preparation, brush removal, and fire lines—making properties safe, functional, and project-ready.</p>
    <h2 class="head" style="left:26px;top:467px;">PROPERTY CLEANUP</h2>
    <p class="copy" style="top:497px;">Quick hauls, debris removal, or full cleanouts—no job too big or small.</p>

    <div class="tag tag--why">Why Choose Us?</div>
    <ul class="list" style="left:26px;top:585px;">
      <li>Locally owned since 2022</li>
      <li>Reliable &amp; affordable – no corners cut</li>
      <li>Professional results you can trust</li>
    </ul>
    <p class="licensed">LICENSED AND INSURED</p>
    <p class="assurances">Quality work <span class="dot">•</span> On Time <span class="dot">•</span> References <span class="dot">•</span> Flexible <span class="dot">•</span> Follow-up</p>

    <div class="divider"></div>

    <div class="tag tag--what">What We Do</div>
    <h2 class="head" style="left:389px;top:318px;">REMOVE</h2>
    <ul class="list" style="left:390px;top:345px;">
      <li>Junk removal</li><li>Trash &amp; waste hauling</li><li>Yard &amp; garden cleanup</li><li>Appliance removal</li>
    </ul>
    <h2 class="head" style="left:388px;top:436px;">INSTALL</h2>
    <ul class="list" style="left:388px;top:463px;">
      <li>Mulch</li><li>DG</li><li>Plants</li><li>Rock</li>
    </ul>
    <h2 class="head" style="left:388px;top:554px;">MAINTENANCE &amp; OTHER</h2>
    <ul class="list" style="left:388px;top:581px;">
      <li>Yard cleanup</li><li>Weed prevention (pre-emergent)</li><li>Roof &amp; gutter cleaning</li><li>Fence &amp; deck staining</li>
    </ul>
    <p class="ask">DON'T SEE? JUST ASK!</p>

    <footer class="contact-bar">
      <p class="contact-bar__cta">CALL OR TEXT TODAY!</p>
      <div class="contact-bar__line">
        <span class="contact-bar__item"><svg viewBox="0 0 16 16" fill="none" stroke="currentColor" stroke-width="1.2"><circle cx="8" cy="8" r="7"/><ellipse cx="8" cy="8" rx="3" ry="7"/><path d="M1 8h14M2.5 4.5h11M2.5 11.5h11"/></svg>www.brackwellyard.example</span>
        <span class="contact-bar__item"><svg viewBox="0 0 16 16" fill="none" stroke="currentColor" stroke-width="1.2"><rect x="1" y="3" width="14" height="10"/><path d="M1 3l7 6 7-6"/></svg>sales@brackwellyard.example</span>
        <span class="contact-bar__item"><svg viewBox="0 0 16 16" fill="none" stroke="currentColor" stroke-width="1.2"><path d="M4 1.5l2.5 3-1.5 2c1 2 2.5 3.5 4.5 4.5l2-1.5 3 2.5-1.5 2.5C7.5 14 2 8.5 1.5 3z"/></svg>(555) 014-7293</span>
      </div>
    </footer>
  </article>

  <!-- Black & white edition -->
  <article class="flyer flyer--mono">
    <header class="masthead">
      <h1 class="masthead__title">TRANSFORMING OUTDOOR SPACES<br>WITH HARD WORK &amp; PRECISION</h1>
      <div class="masthead__brand"><span class="masthead__brand-mark"></span>BRACKWELL YARD SERVICES</div>
    </header>
    <div class="gallery">
      <div class="photo photo--leaves" role="img" aria-label="Black and white: rake leaning on a full leaf bag on a lawn"></div>
      <div class="photo photo--yard" role="img" aria-label="Black and white: backyard with gravel bed, paver wall and fence"></div>
      <div class="photo photo--haul" role="img" aria-label="Black and white: trailer loaded with junk for hauling"></div>
    </div>

    <div class="tag tag--services">Our Services</div>
    <h2 class="head" style="left:26px;top:318px;">LANDSCAPING SERVICES</h2>
    <p class="copy" style="top:349px;">Project-based landscaping to clean, prepare, and transform outdoor spaces with precision.</p>
    <h2 class="head" style="left:26px;top:393px;">GROUND PREPARATION</h2>
    <p class="copy" style="top:423px;">Pad preparation, brush removal, and fire lines—making properties safe, functional, and project-ready.</p>
    <h2 class="head" style="left:26px;top:467px;">PROPERTY CLEANUP</h2>
    <p class="copy" style="top:497px;">Quick hauls, debris removal, or full cleanouts—no job too big or small.</p>

    <div class="tag tag--why">Why Choose Us?</div>
    <ul class="list" style="left:26px;top:585px;">
      <li>Locally owned since 2022</li>
      <li>Reliable &amp; affordable – no corners cut</li>
      <li>Professional results you can trust</li>
    </ul>
    <p class="licensed">LICENSED AND INSURED</p>
    <p class="assurances">Quality work <span class="dot">•</span> On Time <span class="dot">•</span> References <span class="dot">•</span> Flexible <span class="dot">•</span> Follow-up</p>

    <div class="divider"></div>

    <div class="tag tag--what">What We Do</div>
    <h2 class="head" style="left:389px;top:318px;">REMOVE</h2>
    <ul class="list" style="left:390px;top:345px;">
      <li>Junk removal</li><li>Trash &amp; waste hauling</li><li>Yard &amp; garden cleanup</li><li>Appliance removal</li>
    </ul>
    <h2 class="head" style="left:388px;top:436px;">INSTALL</h2>
    <ul class="list" style="left:388px;top:463px;">
      <li>Mulch</li><li>DG</li><li>Plants</li><li>Rock</li>
    </ul>
    <h2 class="head" style="left:388px;top:554px;">MAINTENANCE &amp; OTHER</h2>
    <ul class="list" style="left:388px;top:581px;">
      <li>Yard cleanup</li><li>Weed prevention (pre-emergent)</li><li>Roof &amp; gutter cleaning</li><li>Fence &amp; deck staining</li>
    </ul>
    <p class="ask">DON'T SEE? JUST ASK!</p>

    <footer class="contact-bar">
      <p class="contact-bar__cta">CALL OR TEXT TODAY!</p>
      <div class="contact-bar__line">
        <span class="contact-bar__item"><svg viewBox="0 0 16 16" fill="none" stroke="currentColor" stroke-width="1.2"><circle cx="8" cy="8" r="7"/><ellipse cx="8" cy="8" rx="3" ry="7"/><path d="M1 8h14M2.5 4.5h11M2.5 11.5h11"/></svg>www.brackwellyard.example</span>
        <span class="contact-bar__item"><svg viewBox="0 0 16 16" fill="none" stroke="currentColor" stroke-width="1.2"><rect x="1" y="3" width="14" height="10"/><path d="M1 3l7 6 7-6"/></svg>sales@brackwellyard.example</span>
        <span class="contact-bar__item"><svg viewBox="0 0 16 16" fill="none" stroke="currentColor" stroke-width="1.2"><path d="M4 1.5l2.5 3-1.5 2c1 2 2.5 3.5 4.5 4.5l2-1.5 3 2.5-1.5 2.5C7.5 14 2 8.5 1.5 3z"/></svg>(555) 014-7293</span>
      </div>
    </footer>
  </article>

</div>
</body>
</html>
```